Amber Reed Consulting Business Card

Hi Morwen. Thank you for your work on my coaching business card. I have another business which needs a new card. It is my counselling business. The best way to find out how to approach this project will be to go to my other website. www.amberreedconsulting.example.au and you will be able to see the colours scheme that I will require. White, Green and blue.

The tag line is Amber Reed Consulting So you can look forward to tomorrow. The clients are varied but mostly middle class Australian. The card is to show on it the same details as my other business card but with a different phone number. The tag lines are obviously different. The phone number is 5863 1427 The addresses are all the same.

Again simple, professional sophisticated is best.

Industry/Entity Type

Business

```html
<!DOCTYPE html>
<html lang="en">
<head>
<meta charset="utf-8">
<title>Amber Reed Consulting Business Card</title>
<link rel="stylesheet" href="https://fonts.googleapis.com/css2?family=Michroma&family=Oswald:wght@500&display=swap">
<style>
  :root {
    --backdrop: #e4e6e9;
    --card-white: #ffffff;
    --blue-light: #1f93dc;
    --blue-deep: #1658b0;
    --green: #3fa34d;
    --green-deep: #2b8a3e;
    --ink: #2f3338;
    --ink-soft: #3a3f45;
    --brand-blue: #1d4f9c;
  }
  * { margin: 0; padding: 0; box-sizing: border-box; }
  html, body { width: 1200px; height: 816px; overflow: hidden; }
  body {
    background: var(--backdrop);
    display: flex;
    align-items: center;
    justify-content: center;
  }
  .card {
    position: relative;
    width: 1000px;
    height: 572px;
    border-radius: 40px;
    overflow: hidden;
    background: var(--card-white);
    box-shadow: 0 10px 30px rgba(0,0,0,0.15);
  }
  .card-side-info {
    position: absolute;
    top: 0; right: 0;
    width: 560px;
    height: 100%;
    background: radial-gradient(ellipse at 20% 55%, var(--blue-light) 0%, var(--blue-deep) 100%);
  }
  .card-accent {
    position: absolute;
    left: 440px;
    bottom: 0;
    width: 560px;
    height: 10px;
    background: var(--green);
  }
  .card-pointer {
    position: absolute;
    left: 422px;
    top: 400px;
    width: 20px;
    height: 36px;
  }
  .brand {
    position: absolute;
    left: 40px;
    top: 250px;
    width: 370px;
    text-align: center;
  }
  .brand-line {
    display: flex;
    align-items: center;
    justify-content: center;
    gap: 12px;
  }
  .brand-dot {
    width: 20px; height: 20px;
    border-radius: 50%;
    background: var(--green);
    flex: none;
  }
  .brand-name {
    font-family: "Michroma", sans-serif;
    font-size: 19px;
    color: var(--brand-blue);
    letter-spacing: 0.5px;
    white-space: nowrap;
  }
  .brand-tagline {
    margin-top: 14px;
    font-family: "Michroma", sans-serif;
    font-size: 11px;
    letter-spacing: 0.5px;
    color: var(--green-deep);
  }
  .contact-list {
    position: absolute;
    left: 520px;
    top: 58px;
    list-style: none;
    font-family: "Michroma", sans-serif;
    font-size: 15px;
    color: var(--ink);
    letter-spacing: 1.5px;
    text-transform: uppercase;
  }
  .contact-item { margin-bottom: 14px; }
  .contact-icon { display: block; width: 16px; height: 16px; margin-bottom: 4px; }
  .contact-item p { line-height: 1.35; white-space: nowrap; }
  .contact-web { font-size: 13px; letter-spacing: 1px; }
  .divider {
    position: absolute;
    border-top: 3px dotted var(--ink);
    opacity: 0.8;
  }
  .divider-upper { left: 560px; top: 232px; width: 380px; }
  .divider-lower { left: 520px; top: 318px; width: 260px; }
  .person {
    position: absolute;
    right: 70px;
    top: 336px;
    text-align: right;
    font-family: "Oswald", sans-serif;
    font-weight: 500;
    color: var(--ink-soft);
    text-transform: uppercase;
  }
  .person-name { font-size: 46px; line-height: 1.05; letter-spacing: 1px; }
  .person-role { font-size: 26px; line-height: 1.1; letter-spacing: 1px; }
</style>
</head>
<body>
  <div class="card">
    <div class="card-side-info"></div>
    <div class="card-accent"></div>
    <svg class="card-pointer" viewBox="0 0 20 36" aria-hidden="true">
      <polygon points="20,0 0,18 20,36" fill="#1c82d1"/>
    </svg>

    <div class="brand">
      <div class="brand-line">
        <span class="brand-dot"></span>
        <span class="brand-name">Amber Reed Consulting</span>
      </div>
      <p class="brand-tagline">So you can look forward to tomorrow</p>
    </div>

    <ul class="contact-list">
      <li class="contact-item">
        <svg class="contact-icon" viewBox="0 0 16 16" aria-hidden="true"><path d="M3 1h3l1 4-2 1c1 2 3 4 5 5l1-2 4 1v3c0 1-1 2-2 2C7 15 1 9 1 3c0-1 1-2 2-2z" fill="#2f3338"/></svg>
        <p>5863 1427</p>
      </li>
      <li class="contact-item">
        <svg class="contact-icon" viewBox="0 0 16 16" aria-hidden="true"><rect x="1" y="3" width="14" height="10" fill="#2f3338"/><path d="M1 3l7 6 7-6" stroke="#1a7ccc" stroke-width="1.4" fill="none"/></svg>
        <p>info@yourmail.example</p>
      </li>
      <li class="contact-item">
        <svg class="contact-icon" viewBox="0 0 16 16" aria-hidden="true"><circle cx="8" cy="8" r="7" fill="#2f3338"/><path d="M1 8h14M8 1c-3 3-3 11 0 14M8 1c3 3 3 11 0 14" stroke="#1a7ccc" stroke-width="1.1" fill="none"/></svg>
        <p class="contact-web">www.amberreedconsulting.example.au</p>
      </li>
      <li class="contact-item">
        <svg class="contact-icon" viewBox="0 0 16 16" aria-hidden="true"><path d="M8 1l7 7h-2v7H9v-4H7v4H3V8H1z" fill="#2f3338"/></svg>
        <p>48 Harbour Lane,<br>North Fairview, USA</p>
      </li>
    </ul>

    <div class="divider divider-upper"></div>
    <div class="divider divider-lower"></div>

    <div class="person">
      <p class="person-name">Talia Brenn</p>
      <p class="person-role">General Manager</p>
    </div>
  </div>
</body>
</html>
```